Business Card Design needed for start up company Halvora

In need of a new business card designed for a start up company based in Sydney, Halvora is a new start up innovative Company, our mission it to make property accessible for everyday Australian and to become the leading Real Estate platform in Australia. We want it to be fresh and clean.

Industry/Entity Type

Financial

Contact Information for Business Card

Section for Name
Section for Title

HALVORA - The Strength of Pooling
Mobile:
Direct:

Font styles to use
Sans Serif

Colors
33a6d7
0692cd
0255a3
ffffff

Requirements
Must have
• Logo, all business card details

```html
<!DOCTYPE html>
<html lang="en">
<head>
<meta charset="utf-8">
<title>Halvora Business Card</title>
<link rel="stylesheet" href="https://fonts.googleapis.com/css2?family=Lato:wght@400;700;900&display=swap">
<style>
  :root {
    --page-bg: #e4e6e9;
    --card-top: #f3f6f8;
    --card-top-shade: #e3e9ee;
    --navy: #13214a;
    --navy-deep: #0d1836;
    --band-blue: #1b7db6;
    --band-edge: #33a6d7;
    --mark-blue: #0692cd;
    --circle-blue: #0255a3;
    --ring: #d8dde3;
    --cream: #efe4d2;
    --tag-soft: #e9c9c0;
    --white: #ffffff;
  }
  * { margin: 0; padding: 0; box-sizing: border-box; }
  html, body { width: 1200px; height: 970px; overflow: hidden; }
  body {
    background: var(--page-bg);
    font-family: "Lato", Arial, sans-serif;
    position: relative;
  }
  .business-card {
    position: absolute;
    left: 80px; top: 187px;
    width: 1040px; height: 595px;
    overflow: hidden;
    background: linear-gradient(180deg, var(--card-top) 0%, var(--card-top-shade) 100%);
    box-shadow: 0 14px 40px rgba(20, 30, 50, 0.18);
  }
  .brand {
    position: absolute;
    left: 58px; top: 52px;
    display: flex; align-items: center; gap: 26px;
  }
  .brand-dot {
    width: 176px; height: 176px; border-radius: 50%;
    background: var(--mark-blue);
    flex: none;
  }
  .brand-name {
    font-weight: 900;
    font-size: 112px;
    letter-spacing: -2px;
    color: var(--navy);
    line-height: 1;
  }
  .title-band {
    position: absolute;
    left: 0; top: 305px;
    width: 800px; height: 57px;
    background: linear-gradient(90deg, var(--band-blue), var(--mark-blue));
    border-bottom: 2px solid var(--band-edge);
    clip-path: polygon(0 0, 100% 0, 94% 100%, 0 100%);
    display: flex; align-items: center;
    padding-left: 55px;
  }
  .person-name {
    font-weight: 700; font-size: 34px; color: var(--cream);
    letter-spacing: -0.3px;
  }
  .divider {
    width: 2px; height: 38px; background: var(--cream);
    opacity: 0.7; margin: 0 16px;
  }
  .person-role {
    font-weight: 700; font-size: 28px; color: var(--cream);
  }
  .details-panel {
    position: absolute;
    left: 0; top: 362px;
    width: 100%; height: 233px;
    background: linear-gradient(180deg, #2b4170 0%, var(--navy) 55%, var(--navy-deep) 100%);
  }
  .contact-list {
    position: absolute;
    left: 55px; top: 55px;
    list-style: none;
  }
  .contact-line {
    display: flex; align-items: center; gap: 10px;
    font-size: 29px; color: var(--cream);
    line-height: 32px;
  }
  .contact-icon {
    width: 28px; height: 28px; flex: none;
  }
  .tagline {
    position: absolute;
    left: 55px; top: 148px;
    font-size: 28px; color: var(--tag-soft);
  }
  .tagline strong { font-weight: 700; color: var(--cream); }
  .corner-circle {
    position: absolute;
    left: 705px; top: 272px;
    width: 350px; height: 350px;
    border-radius: 50%;
    background: var(--ring);
    display: flex; align-items: center; justify-content: center;
  }
  .corner-circle::after {
    content: "";
    width: 310px; height: 310px; border-radius: 50%;
    background: radial-gradient(circle at 40% 35%, #1c76c0 0%, var(--circle-blue) 70%);
  }
</style>
</head>
<body>
  <div class="business-card">
    <div class="brand">
      <div class="brand-dot"></div>
      <div class="brand-name">HALVORA</div>
    </div>

    <div class="details-panel">
      <ul class="contact-list">
        <li class="contact-line">
          <svg class="contact-icon" viewBox="0 0 28 28" aria-label="Mobile">
            <rect width="28" height="28" fill="#1b7db6"/>
            <rect x="9" y="4" width="10" height="20" rx="1.5" fill="none" stroke="#efe4d2" stroke-width="1.8"/>
            <rect x="11" y="7" width="6" height="7" fill="#efe4d2"/>
          </svg>
          <span>312.845.6072</span>
        </li>
        <li class="contact-line">
          <svg class="contact-icon" viewBox="0 0 28 28" aria-label="Direct">
            <rect width="28" height="28" fill="#1b7db6"/>
            <path d="M5 11 C5 6 23 6 23 11 L19 12 L18 9 L10 9 L9 12 Z" fill="#efe4d2"/>
            <path d="M8 14 L20 14 L22 22 L6 22 Z" fill="#efe4d2"/>
            <circle cx="14" cy="18" r="2" fill="#1b7db6"/>
          </svg>
          <span>312.845.6072</span>
        </li>
      </ul>
      <p class="tagline"><strong>HALVORA</strong> - The Strength of Pooling</p>
    </div>

    <div class="title-band">
      <span class="person-name">LIAM PORTER</span>
      <span class="divider"></span>
      <span class="person-role">Managing Director</span>
    </div>

    <div class="corner-circle"></div>
  </div>
</body>
</html>
```